Business Card Design

Business Card for professional consulting firm working with large financial institutions.

Target Market(s)

Executive buyers

Industry/Entity Type

Banking

Contact Information for Business Card

Mild creativity wanted. Not boring, but do elaborate artwork.

Font styles to use
Serif
Sans Serif

Colors

Designer to choose colors to be used in the design.

Requirements
Must have
• Standard business card features - company name, individual name, telephone, website, email, locations.
Nice to have
• Two colors
Should not have
• too many colors, fancy printing, cartoons.

```html
<!DOCTYPE html>
<html lang="en">
<head>
<meta charset="utf-8">
<title>Northgate Partners Business Card</title>
<link href="https://fonts.googleapis.com/css2?family=Lato:wght@400;700&display=swap" rel="stylesheet">
<style>
  :root {
    --navy: #022d84;
    --grey-panel: #c0c0c0;
    --grey-rule: #bdbdbd;
    --ink: #1f1f1f;
    --paper: #ffffff;
    --backdrop: #8a8a8a;
  }
  * { margin: 0; padding: 0; box-sizing: border-box; }
  html, body { width: 1200px; height: 1200px; overflow: hidden; }
  body { background: var(--backdrop); position: relative; font-family: "Lato", sans-serif; }

  .card { position: absolute; top: 310px; height: 594px; box-shadow: 2px 3px 6px rgba(0,0,0,.35); }
  .card--front { left: 234px; width: 364px; background: var(--paper); text-align: center; color: var(--ink); }
  .card--back { left: 627px; width: 370px; background: var(--grey-panel); overflow: hidden; }

  .company-name { font-family: "Lato", sans-serif; font-size: 30px; font-weight: 400; letter-spacing: .3px; }
  .card--front .company-name { position: absolute; top: 158px; left: 0; right: 0; color: var(--navy); }

  .person { position: absolute; top: 313px; left: 0; right: 0; }
  .person__name { font-size: 21px; font-weight: 700; color: var(--navy); letter-spacing: .2px; }
  .person__title { font-size: 16.5px; margin-top: 1px; }

  .contact-icons { position: absolute; top: 373px; left: 88px; width: 189px; height: 24px; }

  .contact { position: absolute; top: 408px; left: 0; right: 0; font-size: 16.5px; line-height: 22px; }
  .divider { position: absolute; top: 489px; left: 87px; width: 190px; height: 2px; background: var(--grey-rule); }
  .address { position: absolute; top: 507px; left: 0; right: 0; font-size: 16.5px; line-height: 22px; }

  .back-panel { position: absolute; inset: 0; }
  .card--back .company-name { position: absolute; top: 474px; left: 0; right: 0; text-align: center; color: var(--paper); }
</style>
</head>
<body>
  <section class="card card--front">
    <div class="company-name">Northgate Partners</div>

    <div class="person">
      <div class="person__name">JONATHAN SMITH</div>
      <div class="person__title">Managing Director</div>
    </div>

    <svg class="contact-icons" viewBox="0 0 189 24" aria-hidden="true">
      <line x1="0" y1="12" x2="54" y2="12" stroke="#222" stroke-width="1.2"/>
      <line x1="135" y1="12" x2="189" y2="12" stroke="#222" stroke-width="1.2"/>
      <g fill="var(--navy)">
        <circle cx="67" cy="12" r="12"/>
        <circle cx="94.5" cy="12" r="12"/>
        <circle cx="122" cy="12" r="12"/>
      </g>
      <g fill="#fff" stroke="#fff">
        <path d="M60 12c0-3 3-5 7-5s7 2 7 5l-2 1-2-1v-1h-6v1l-2 1z" stroke="none"/>
        <rect x="62" y="13" width="10" height="5" rx="1" stroke="none"/>
        <rect x="88" y="7.5" width="13" height="9" fill="none" stroke-width="1.5"/>
        <path d="M88.5 8l6 4.8 6-4.8" fill="none" stroke-width="1.2"/>
        <circle cx="122" cy="12" r="6" fill="none" stroke-width="1.4"/>
        <path d="M116 12h12M122 6c-3 3-3 9 0 12M122 6c3 3 3 9 0 12" fill="none" stroke-width="1"/>
      </g>
    </svg>

    <div class="contact">
      <div>044-123 456 789</div>
      <div>info@webname.com</div>
      <div>www.websitename.com</div>
    </div>
    <div class="divider"></div>
    <div class="address">
      <div>12345, Address Goes Here</div>
      <div>Country Name, 123456</div>
    </div>
  </section>

  <section class="card card--back">
    <svg class="back-panel" viewBox="0 0 370 594" preserveAspectRatio="none" aria-hidden="true">
      <path d="M0 286 C120 200 250 130 370 100 L370 114 C250 144 120 214 0 300 Z" fill="#ffffff"/>
      <path d="M0 300 C120 214 250 144 370 114 L370 594 L0 594 Z" fill="var(--navy)"/>
    </svg>
    <div class="company-name">Northgate Partners</div>
  </section>
</body>
</html>
```